New Business Card Design for Manufacturing

We are an engineering/manufacturing company that offers Advanced machining/assembly/engineering services, as well as innovative products for the heavy duty engine cooling markets.

We are looking to get a new business card designed that is clean and modern looking, but still fits the wide range of technical/skilled work we do.

- We hope to use this design as the base for other design work in new Presentations, web, and print work.

Industry/Entity Type

Engineering

Contact Information for Business Card

Our preferred color of blue is (RGB) 22/71/159 but can vary slightly from that color. Our content will be our Logo and full company name (Vantrell Forge Works, Inc.), company address, name, job title, phone number with extension, cell number, fax number, website, and email address on the cards.
We'd like the full company name next to the logo, but we are open to other interpretations of that layout.
Preferably, we would like the back side to be clean with just our logo, and the front to contain all of the contact information.

Colors
2f74b4
0355a3
85abd2

Requirements
Must have
• - Logo, company name, needed content - We are open to interpretation beyond that.
• - Standard size business card.
• - Horizontal orientation.
• - Enough space for lengthy names / job titles (for example, a job title could read "Directory of Human Resources" or "V.P. of Governmental Affairs"). We need this to look clean, whether the title be short (CEO) or long (as described above).

```html
<!DOCTYPE html>
<html lang="en">
<head>
<meta charset="utf-8">
<title>Vantrell Forge Works – Business Card</title>
<link href="https://fonts.googleapis.com/css2?family=Lato:wght@400;700;900&display=swap" rel="stylesheet">
<style>
  :root {
    --brand-blue: #16479f;
    --card-gray: #7c8388;
    --band-gray: #858b90;
    --paper: #ffffff;
    --ink: #3a3d40;
    --stage: #e9eaec;
  }
  * { margin: 0; padding: 0; box-sizing: border-box; }
  html, body { width: 1200px; height: 930px; overflow: hidden; }
  body {
    background: var(--stage);
    font-family: "Lato", Arial, sans-serif;
    position: relative;
  }
  .card {
    position: absolute;
    width: 620px;
    height: 354px;
    overflow: hidden;
    box-shadow: 0 6px 18px rgba(0,0,0,0.18);
  }

  /* Back side */
  .card-back { left: 80px; top: 90px; background: var(--card-gray); color: var(--paper); }
  .card-back .brand { position: absolute; left: 150px; top: 126px; }
  .card-back .website {
    position: absolute; right: 150px; bottom: 56px;
    font-size: 14px; letter-spacing: 1px;
  }

  /* Brand lockup */
  .brand { display: flex; align-items: center; gap: 14px; }
  .brand-square { width: 38px; height: 38px; background: currentColor; flex: none; }
  .brand-name {
    font-weight: 900; font-size: 21px; line-height: 1.02;
    text-transform: uppercase; letter-spacing: 0.3px;
  }

  /* Front side */
  .card-front { left: 500px; top: 486px; background: var(--paper); }
  .card-front .brand { position: absolute; left: 44px; top: 150px; color: var(--brand-blue); }
  .divider {
    position: absolute; left: 352px; top: 96px;
    width: 2px; height: 170px; background: var(--brand-blue);
  }
  .contact { position: absolute; left: 372px; top: 84px; color: var(--ink); }
  .person-name {
    color: var(--brand-blue); font-size: 22px; font-weight: 400;
    text-transform: uppercase; letter-spacing: 1px; line-height: 1.05;
  }
  .job-title { font-size: 14px; margin-bottom: 12px; }
  .address { font-size: 14px; line-height: 1.3; margin-bottom: 10px; }
  .contact-list { list-style: none; font-size: 13.5px; line-height: 1.3; }
  .contact-list li { display: flex; align-items: center; gap: 8px; }
  .contact-list svg { width: 9px; height: 9px; flex: none; fill: var(--brand-blue); }
  .footer-bands { position: absolute; left: 0; bottom: 0; width: 620px; height: 60px; }
</style>
</head>
<body>

  <section class="card card-back" aria-label="Business card back">
    <div class="brand">
      <span class="brand-square"></span>
      <span class="brand-name">Vantrell<br>Forge Works<br>Inc.</span>
    </div>
    <p class="website">www.vantrellforge.com</p>
  </section>

  <section class="card card-front" aria-label="Business card front">
    <div class="brand">
      <span class="brand-square"></span>
      <span class="brand-name">Vantrell<br>Forge Works<br>Inc.</span>
    </div>

    <div class="divider"></div>

    <div class="contact">
      <h1 class="person-name">Dorian Velasco</h1>
      <p class="job-title">Directory of Human Resources</p>
      <p class="address">480 Harlow Ridge Rd.<br>Brinmoor, OH 44870</p>
      <ul class="contact-list">
        <li><svg viewBox="0 0 10 10"><path d="M2 0h2l1 3-1.5 1a6 6 0 0 0 2.5 2.5L7 5l3 1v2a2 2 0 0 1-2 2A8 8 0 0 1 0 2a2 2 0 0 1 2-2z"/></svg>1234- ext</li>
        <li><svg viewBox="0 0 10 10"><path d="M2.5 0h5a1 1 0 0 1 1 1v8a1 1 0 0 1-1 1h-5a1 1 0 0 1-1-1V1a1 1 0 0 1 1-1zm.5 1.5v6h4v-6z"/></svg>555-318-4062</li>
        <li><svg viewBox="0 0 10 10"><rect x="0" y="3" width="10" height="5" rx="1"/><rect x="2.5" y="0" width="5" height="3"/><rect x="2.5" y="7" width="5" height="3" fill="#fff"/></svg>(555)318-4063</li>
        <li><svg viewBox="0 0 10 10"><path d="M0 2h10v6H0zm1 1v.3l4 2.5 4-2.5V3z"/></svg>hello@vantrellforge.com</li>
        <li><svg viewBox="0 0 10 10"><circle cx="5" cy="5" r="4.2" fill="none" stroke="#16479f" stroke-width="1.2"/><path d="M0.8 5h8.4M5 0.8c-2.4 2.6-2.4 5.8 0 8.4M5 0.8c2.4 2.6 2.4 5.8 0 8.4" fill="none" stroke="#16479f" stroke-width="0.9"/></svg>www.vantrellforge.com</li>
      </ul>
    </div>

    <svg class="footer-bands" viewBox="0 0 620 60" aria-hidden="true">
      <polygon points="0,46 385,46 379,60 0,60" fill="var(--band-gray)"/>
      <polygon points="385,46 395,22 395,60 379,60" fill="var(--band-gray)"/>
      <polygon points="402,10 620,10 620,60 390,60" fill="var(--brand-blue)"/>
    </svg>
  </section>

</body>
</html>
```